Lanternfield Drinks business cards

We need a business card design for our new logo. The company is modern, progressive, professional, yet approachable. The key products are ready to drink bottles and cans of coffee based beverages.
These cards will be a critical part of the first impression made by our sales organization, business development team, and all external facing personnel.
Card can be a vertical or horizontal orientation.

Target Market(s)

Customers, suppliers, business partners

Industry/Entity Type

Business

Contact Information for Business Card

Business cards should feature Company Name and Logo.

Font styles to use
Serif

Colors

Designer to choose colors to be used in the design.

Requirements
Must have
• Strong readability of Name, phone #, mobile number and email address.
• Job title, website url, Street Address, and other details can be secondary level readability.
Nice to have
• High impact, simplistic quality design.
• Ok to utilize the 'H in the box' separate from the company name

```html
<!DOCTYPE html>
<html lang="en">
<head>
<meta charset="utf-8">
<title>Lanternfield Drinks – Business Cards</title>
<link rel="stylesheet" href="https://fonts.googleapis.com/css2?family=Lato:wght@400;700&display=swap">
<style>
  :root {
    --backdrop: #7a7a7a;
    --brand-orange: #f05a2e;
    --card-white: #ffffff;
    --ink-white: #ffffff;
    --shadow: rgba(0, 0, 0, 0.45);
  }
  * { box-sizing: border-box; margin: 0; padding: 0; }
  html, body {
    width: 1200px; height: 900px; overflow: hidden;
    background: var(--backdrop);
    font-family: "Lato", Arial, sans-serif;
  }
  .stage { position: relative; width: 1200px; height: 900px; }

  .card {
    position: absolute; top: 200px; width: 310px; height: 502px;
    box-shadow: 3px 4px 6px var(--shadow);
  }
  .card--front {
    left: 265px; background: var(--brand-orange);
    border-radius: 58px 0 58px 0; color: var(--ink-white);
  }
  .card--back {
    left: 641px; background: var(--card-white);
    border-radius: 0 58px 0 58px;
  }

  .brand-block { position: absolute; left: 28px; top: 45px; }
  .brand-square {
    width: 62px; height: 62px; border: 6px solid var(--ink-white);
  }
  .brand-name {
    margin-top: 18px; font-weight: 700; font-size: 24px; line-height: 1.15;
    letter-spacing: 0.5px; color: var(--ink-white);
  }

  .contact { position: absolute; left: 25px; top: 286px; }
  .person-name { font-weight: 700; font-size: 20px; letter-spacing: 0.3px; }
  .person-title { font-size: 14.5px; margin-top: 2px; }
  .contact-list { list-style: none; margin-top: 9px; font-size: 14.5px; }
  .contact-list li { display: flex; align-items: center; height: 17.5px; }
  .contact-list svg { width: 12px; height: 12px; margin-right: 6px; fill: var(--ink-white); flex: none; }
  .address { display: flex; margin-top: 8px; font-size: 14.5px; line-height: 18px; }
  .address svg { width: 12px; height: 14px; margin: 2px 3px 0 0; fill: var(--ink-white); flex: none; }

  .back-wordmark {
    position: absolute; left: 144px; top: 34px; height: 330px;
    writing-mode: vertical-rl; transform: rotate(180deg);
    font-weight: 700; font-size: 30px; letter-spacing: 1px;
    color: var(--brand-orange); text-align: center; white-space: nowrap;
  }
  .back-square {
    position: absolute; left: 109px; top: 372px; width: 92px; height: 92px;
    border: 7px solid var(--brand-orange);
  }
</style>
</head>
<body>
<main class="stage">
  <section class="card card--front" aria-label="Card front">
    <div class="brand-block">
      <div class="brand-square"></div>
      <p class="brand-name">LANTERNFIELD<br>DRINKS</p>
    </div>
    <div class="contact">
      <h1 class="person-name">LORUM SMITH</h1>
      <p class="person-title">Managing Director</p>
      <ul class="contact-list">
        <li><svg viewBox="0 0 12 12"><path d="M1 4c0-2 2-3 5-3s5 1 5 3v1H8V4H4v1H1zM2 6h8l1 5H1z"/></svg>444 555 6688</li>
        <li><svg viewBox="0 0 12 12"><path d="M3 0h6v12H3zM4 1.5v8h4v-8z"/></svg>888 555 4433</li>
        <li><svg viewBox="0 0 12 12"><path d="M0 2h12v1L6 7 0 3zM0 4.5l6 4 6-4V10H0z"/></svg>info@webname.com</li>
        <li><svg viewBox="0 0 12 12"><circle cx="6" cy="6" r="6"/></svg>www.webaddress.com</li>
      </ul>
      <div class="address">
        <svg viewBox="0 0 12 14"><path d="M6 0a5 5 0 0 1 5 5c0 4-5 9-5 9S1 9 1 5a5 5 0 0 1 5-5zm0 3a2 2 0 1 0 0 4 2 2 0 0 0 0-4z"/></svg>
        <p>421, Address line here,<br>Dummy Code, 45452<br>Country Name</p>
      </div>
    </div>
  </section>

  <section class="card card--back" aria-label="Card back">
    <p class="back-wordmark">LANTERNFIELD DRINKS</p>
    <div class="back-square"></div>
  </section>
</main>
</body>
</html>
```